Professional Photography Business cards

I need business cards that include my logo which I have uploaded. I run a photography business. I am open to ideas but I would like one side to have my logo and the other side to have my contact info. I don't have a website made but I do own a website domain. I have uploaded 2 different logo color schemes. My business colors are Blue, black , and white.

Business Name
Business Phone Number
Business Email
Business Website address
Instagram

Industry/Entity Type

Professional Photography

Contact Information for Business Card

Phone Number: 916-384-7702 email: info@tlane-studio.example Instagram: @t.lanestudio website doman- www.tlane-studio.example

Requirements
Must have
• I like the idea of a business card with a full black background front and back of card. My colors must include royal blue, black, and white

```html
<!DOCTYPE html>
<html lang="en">
<head>
<meta charset="utf-8">
<title>T. Lane Studio — Business Cards</title>
<link rel="stylesheet" href="https://fonts.googleapis.com/css2?family=Montserrat:wght@700&family=Roboto:wght@300;400;500&display=swap">
<style>
  :root {
    --royal: #3346c9;
    --royal-deep: #2a3aa8;
    --ink: #0b0b0b;
    --ink-soft: #1a1a1a;
    --paper: #ffffff;
    --muted: #c9c9c9;
    --backdrop: #3b3b3b;
  }
  * { box-sizing: border-box; margin: 0; padding: 0; }
  html, body { width: 1200px; height: 929px; overflow: hidden; }
  body {
    background: var(--backdrop);
    font-family: "Roboto", sans-serif;
    display: flex;
    align-items: center;
    justify-content: center;
    gap: 44px;
  }
  .card {
    width: 540px;
    height: 309px;
    border-radius: 16px;
    position: relative;
    overflow: hidden;
    background: linear-gradient(135deg, var(--ink) 0%, var(--ink-soft) 100%);
    box-shadow: 0 14px 34px rgba(0,0,0,.55);
  }

  /* Brand name */
  .brand {
    display: flex;
    align-items: center;
    gap: 14px;
    font-family: "Roboto", sans-serif;
    font-weight: 400;
    letter-spacing: .04em;
    color: var(--paper);
  }
  .brand__dot {
    border-radius: 50%;
    border: 3px solid var(--royal);
  }

  /* Front */
  .card--front {
    display: flex;
    align-items: center;
    justify-content: center;
  }
  .card--front .brand { font-size: 38px; }
  .card--front .brand__dot { width: 44px; height: 44px; }

  /* Back */
  .card--back .brand {
    position: absolute;
    left: 34px;
    top: 106px;
    font-size: 22px;
    gap: 10px;
  }
  .card--back .brand__dot { width: 26px; height: 26px; border-width: 2px; }
  .divider {
    position: absolute;
    left: 258px;
    top: 40px;
    width: 1.5px;
    height: 156px;
    background: var(--royal);
  }
  .contact {
    position: absolute;
    left: 282px;
    top: 34px;
  }
  .contact__name {
    font-family: "Montserrat", sans-serif;
    font-weight: 700;
    font-size: 20px;
    line-height: 24px;
    color: var(--royal);
    letter-spacing: -.01em;
  }
  .contact__role {
    font-weight: 400;
    font-size: 15px;
    line-height: 20px;
    color: var(--muted);
    margin-top: 2px;
    margin-bottom: 12px;
  }
  .contact__list { list-style: none; }
  .contact__item {
    display: flex;
    align-items: center;
    gap: 8px;
    font-size: 14px;
    font-weight: 300;
    color: var(--paper);
    line-height: 22px;
  }
  .contact__icon { width: 13px; height: 13px; flex: none; }
  .band {
    position: absolute;
    left: 0; right: 0;
    top: 214px;
    height: 52px;
    background: var(--royal-deep);
    color: var(--paper);
    font-size: 19px;
    font-weight: 500;
    display: flex;
    align-items: center;
    justify-content: center;
    letter-spacing: .01em;
  }
</style>
</head>
<body>
  <section class="card card--front" aria-label="Card front">
    <div class="brand"><span class="brand__dot"></span>T. Lane Studio</div>
  </section>

  <section class="card card--back" aria-label="Card back">
    <div class="brand"><span class="brand__dot"></span>T. Lane Studio</div>
    <div class="divider"></div>
    <div class="contact">
      <h1 class="contact__name">TESSA LANE</h1>
      <p class="contact__role">Photographer</p>
      <ul class="contact__list">
        <li class="contact__item">
          <svg class="contact__icon" viewBox="0 0 16 16" fill="var(--royal)"><path d="M3.5 1.5l2.5 0 1 3.5-1.8 1.2a8 8 0 0 0 4.6 4.6L11 9l3.5 1v2.5c0 1-1 2-2 2A11 11 0 0 1 1.5 3.5c0-1 1-2 2-2z"/></svg>
          916.384.7702
        </li>
        <li class="contact__item">
          <svg class="contact__icon" viewBox="0 0 16 16" fill="none" stroke="var(--royal)" stroke-width="1.8"><rect x="1" y="3" width="14" height="10"/><path d="M1 3l7 6 7-6"/></svg>
          info@tlane-studio.example
        </li>
        <li class="contact__item">
          <svg class="contact__icon" viewBox="0 0 16 16" fill="none" stroke="var(--royal)" stroke-width="1.8"><circle cx="8" cy="8" r="6"/></svg>
          @t.lanestudio
        </li>
        <li class="contact__item">
          <svg class="contact__icon" viewBox="0 0 16 16" fill="none" stroke="var(--royal)" stroke-width="1.5"><circle cx="8" cy="8" r="6.5"/><ellipse cx="8" cy="8" rx="2.8" ry="6.5"/><path d="M1.5 8h13"/></svg>
          www.tlane-studio.example
        </li>
      </ul>
    </div>
    <div class="band">4127 Alder Creek Road Fairview, Oh 45210</div>
  </section>
</body>
</html>
```